Postcard Design

business name: COZY HOUR HELPER. I am a mother of 2 well adjusted, successful teenage boys. I decided to start this company caring for kids who are home sick, unable to go to daycare or school, and when their parent cant stay home with them. I was also a career woman for many years, with no friends available or family nearby to help when i was in an emergency situation for childcare. I know how stressful it can be when a child gets sick suddenly and unexpectedly. I would like to help out those parents in need, that have pressing schedules and a sick child at home that they really want to take care of, but cant due to their work pressures and priorities. I want parents to know that their child is safe and I can help them when in need, at last minute. The design should show the child is safe and well cared for and the parent is at ease, able to accomplish their obligations. I have also founded a nonprofit environmental education program in which I teach children in youth summer camps. I have taught creativity arts combined with science curriculum in kindergarten to 8th grade non-formal teaching for the past 5 years. This is a small community, and many people know me. I will be handing out these postcards to local daycares and people I know.

Industry/Entity Type

Business

```html
<!DOCTYPE html>
<html lang="en">
<head>
<meta charset="utf-8">
<title>Cozy Hour Helper – Postcard</title>
<link href="https://fonts.googleapis.com/css2?family=Nunito:wght@800;900&family=Roboto+Condensed:wght@400;700&display=swap" rel="stylesheet">
<style>
  :root{
    --stage:#ece6dc;
    --navy:#283a80;
    --pink:#e0466f;
    --green:#c9e3a4;
    --green-light:#e4f1cf;
    --orange:#e98a2a;
    --text:#333333;
    --white:#ffffff;
  }
  *{box-sizing:border-box;margin:0;padding:0}
  html,body{width:1200px;height:500px;overflow:hidden}
  body{background:var(--stage);position:relative;font-family:"Roboto Condensed",Arial,sans-serif;color:var(--text)}

  .card{position:absolute;top:37px;width:560px;height:430px;overflow:hidden;box-shadow:0 3px 10px rgba(0,0,0,.25)}
  .card--front{left:27px;background:var(--green)}
  .card--back{left:613px;background:var(--green)}

  /* front */
  .front-photo{position:absolute;inset:0 0 auto 0;height:330px;
    background:linear-gradient(120deg,#f4efe9 0%,#ffffff 35%,#eadbd0 60%,#f6f1ec 100%)}
  .front-curve{position:absolute;left:0;top:0;width:560px;height:430px}
  .headline{position:absolute;left:150px;top:18px;width:350px;text-align:center;
    font-family:"Nunito",Arial,sans-serif;font-weight:900;font-size:29px;line-height:30px;color:var(--navy)}
  .brand{position:absolute;font-family:"Nunito",Arial,sans-serif;font-weight:900;color:var(--navy);text-align:center;line-height:1}
  .brand--front{left:300px;top:212px;width:240px;font-size:27px}
  .portrait{position:absolute;left:20px;top:204px;width:198px;height:198px;border-radius:50%;
    border:6px solid var(--orange);background:radial-gradient(circle at 50% 45%,#f3efe9 0%,#cfc7c0 55%,#8b8682 100%)}
  .front-copy{position:absolute;left:236px;top:318px;width:290px;text-align:center;
    font-weight:700;font-size:19px;line-height:22px;color:var(--navy)}
  .phone{display:flex;align-items:center;justify-content:center;gap:6px;font-weight:700}
  .phone--front{position:absolute;left:236px;top:392px;width:290px;font-size:20px;color:var(--pink)}
  .phone svg{width:18px;height:18px}

  /* back */
  .back-text{position:absolute;left:0;top:0;width:345px;height:430px;
    background:linear-gradient(90deg,var(--green-light) 0%,#ffffff 55%,#ffffff 100%);
    clip-path:polygon(0 0,310px 0,322px 215px,345px 430px,0 430px);padding:20px 0 0 38px}
  .back-title{width:230px;font-weight:700;font-size:15.5px;line-height:17px;color:var(--pink);margin-bottom:12px}
  .back-sub{font-weight:700;font-size:12.5px;margin-bottom:9px}
  .back-body{width:250px;font-size:12px;line-height:15.5px;margin-bottom:13px}
  .back-body strong{font-weight:700}
  .phone--back{width:250px;font-size:17px;color:var(--navy);margin-top:2px}
  .web{width:250px;text-align:center;font-size:12px;margin-top:2px}
  .brand--back{left:310px;top:32px;width:230px;font-size:25px}
  .photo{position:absolute;left:312px;width:225px}
  .photo--team{top:103px;height:80px;background:linear-gradient(90deg,#dcd8d4,#f1efec,#c9c4c0)}
  .photo--checkup{top:193px;height:93px;background:linear-gradient(90deg,#e9e7ea,#f5f2f0,#d9d4d8)}
  .photo--rest{top:296px;height:122px;background:linear-gradient(120deg,#f4eedd,#f7e4ea,#e8d5cc)}
</style>
</head>
<body>

<section class="card card--front">
  <div class="front-photo" role="img" aria-label="Photo of a sick young child resting in bed while a parent's hand checks their forehead"></div>
  <svg class="front-curve" viewBox="0 0 560 430" aria-hidden="true">
    <path d="M0 300 Q250 330 560 300 L560 430 L0 430 Z" fill="var(--green)"/>
    <path d="M0 300 Q250 330 560 300" fill="none" stroke="var(--navy)" stroke-width="2.5"/>
  </svg>
  <h1 class="headline">You don’t have to take the day off again</h1>
  <div class="brand brand--front">COZY HOUR HELPER</div>
  <div class="portrait" role="img" aria-label="Photo of a smiling working mother in an office meeting"></div>
  <p class="front-copy">If your child is sick and cannot go to school or regular day care, and you need to be at work, call for help at</p>
  <p class="phone phone--front">
    <svg viewBox="0 0 20 20" aria-hidden="true"><circle cx="10" cy="10" r="9" fill="none" stroke="currentColor" stroke-width="1.4"/><path d="M7 5.5l1.6 2.4-1 1.2a6 6 0 0 0 3.3 3.3l1.2-1 2.4 1.6-.9 1.6C9 14 6 11 5.4 6.4z" fill="currentColor"/></svg>
    (555) 214.7390
  </p>
</section>

<section class="card card--back">
  <div class="back-text">
    <h2 class="back-title">Sick child care is offered to parents whose children are temporarily ill</h2>
    <h3 class="back-sub">Sick Child Care at Home</h3>
    <p class="back-body">All parents have experienced a time when they have needed trustworthy, emergency care for a child who cannot attend school or for a precious little one with a cold or flu that cannot go to daycare. During this critical time, while the child is recuperating, parents can trust <strong>Cozy Hour Helper</strong> who is experienced in providing compassionate care.</p>
    <p class="back-body">We understand that sick child care requires more sensitivity and training than typical babysitting. When you select someone to provide sick child care, remember that our Nannies are trained and experienced in providing compassionate care.</p>
    <p class="back-body">For your last minute request or a booked well in advance to cover your hectic schedule, call us at</p>
    <p class="phone phone--back">
      <svg viewBox="0 0 20 20" aria-hidden="true"><circle cx="10" cy="10" r="9" fill="none" stroke="currentColor" stroke-width="1.4"/><path d="M7 5.5l1.6 2.4-1 1.2a6 6 0 0 0 3.3 3.3l1.2-1 2.4 1.6-.9 1.6C9 14 6 11 5.4 6.4z" fill="currentColor"/></svg>
      (555) 214.7390
    </p>
    <p class="web">cozyhourhelper.example/care</p>
  </div>
  <div class="brand brand--back">COZY HOUR HELPER</div>
  <div class="photo photo--team" role="img" aria-label="Photo of smiling professionals in a business meeting"></div>
  <div class="photo photo--checkup" role="img" aria-label="Photo of a child in bed having their temperature taken"></div>
  <div class="photo photo--rest" role="img" aria-label="Photo of a little girl resting in bed with a cool cloth on her forehead"></div>
</section>

</body>
</html>
```